Business Card Re-Design/Update

We'd like to update out business cards. I've included our current "Style guide" which has the colour scheme of the organisation in it. I've also included the branding files with logos etc in them.

I've also included a copy of one of our existing cards so that you can see how ugly/dated they look. I'd like a fresh modern corporate look.

Target Market(s)

These are for our clients, potential clients, industry contacts - like all business cards

Contact Information for Business Card

Name
Position
Company Address - Level 1, 47 Fernby Street, Carlow Qld 4072
Direct Phone
mobile
Email
Website -www.korvalit.com.au
Logo

Colors

Designer to choose colors to be used in the design.

Requirements
Must have
• Main Logo
• Cards will need to be editable to be able to personalize them for each new employee.
Nice to have
• The MapOut, ShipWell, KeepSteady would be okay to have if they can be sensibly and professionally added to the look without detracting from the main imagery.
• Maybe they could go on the back of the card? will leave this to your creative discretion as to whether/where they fit.
Should not have
• Should not have decorative or script fonts

```html
<!DOCTYPE html>
<html lang="en">
<head>
<meta charset="utf-8">
<title>korvalit business card</title>
<link rel="stylesheet" href="https://fonts.googleapis.com/css2?family=Roboto:wght@400;500;700&family=Roboto+Condensed:wght@400;700&display=swap">
<style>
  :root {
    --backdrop: #2a2a2b;
    --card-front: #f3f3f3;
    --card-back: #231f20;
    --brand-red: #c4161c;
    --ink: #1d1d1d;
    --ink-soft: #555555;
    --rule: #9a9a9a;
    --white: #ffffff;
    --green: #5fa53c;
    --blue: #2b8fd6;
    --magenta: #c2268f;
  }
  * { margin: 0; padding: 0; box-sizing: border-box; }
  html, body { width: 1200px; height: 960px; overflow: hidden; }
  body { background: var(--backdrop); font-family: "Roboto", sans-serif; position: relative; }

  .card { position: absolute; width: 600px; height: 342px; }
  .card--front { left: 322px; top: 108px; background: var(--card-front); }
  .card--back { left: 320px; top: 493px; background: var(--card-back); }

  .brand { position: absolute; display: flex; align-items: center; }
  .brand__mark { background: var(--brand-red); }
  .brand__name { font-family: "Roboto", sans-serif; font-weight: 700; letter-spacing: -0.5px; line-height: 1; }

  .card--front .brand { right: 36px; top: 34px; gap: 12px; }
  .card--front .brand__mark { width: 30px; height: 30px; }
  .card--front .brand__name { font-size: 32px; color: var(--ink); }

  .person { position: absolute; left: 31px; top: 135px; }
  .person__name { font-family: "Roboto Condensed", sans-serif; font-weight: 700; font-size: 21px; color: var(--brand-red); line-height: 1.1; }
  .person__role { font-family: "Roboto Condensed", sans-serif; font-size: 15px; color: var(--ink); margin-top: 2px; }

  .contact { position: absolute; left: 31px; top: 190px; list-style: none; }
  .contact__item { display: flex; align-items: center; gap: 8px; height: 19px; font-size: 14px; color: var(--ink-soft); }
  .contact__icon { width: 13px; height: 13px; fill: var(--brand-red); flex: none; }

  .address { position: absolute; right: 38px; top: 248px; text-align: right; font-size: 14px; line-height: 19px; color: var(--ink-soft); }

  .card__rule { position: absolute; left: 0; right: 0; top: 310px; height: 1px; background: var(--rule); }
  .web-band { position: absolute; left: 326px; top: 295px; width: 238px; height: 28px; background: var(--brand-red); color: var(--white); font-size: 13px; letter-spacing: 1.6px; display: flex; align-items: center; justify-content: center; }

  .card--back .brand { left: 0; right: 0; top: 118px; justify-content: center; gap: 20px; }
  .card--back .brand__mark { width: 66px; height: 66px; }
  .card--back .brand__name { font-size: 56px; color: var(--white); }

  .services { position: absolute; left: 0; right: 0; top: 274px; display: flex; justify-content: center; gap: 40px; list-style: none; }
  .service { display: flex; align-items: center; gap: 8px; font-size: 27px; font-weight: 500; letter-spacing: -0.5px; }
  .service__mark { width: 20px; height: 20px; }
  .service--map { color: var(--green); } .service--map .service__mark { background: var(--green); }
  .service--ship { color: var(--blue); } .service--ship .service__mark { background: var(--blue); }
  .service--keep { color: var(--magenta); } .service--keep .service__mark { background: var(--magenta); }
</style>
</head>
<body>

<section class="card card--front" aria-label="Business card front">
  <div class="brand">
    <span class="brand__mark"></span>
    <span class="brand__name">korvalit</span>
  </div>

  <div class="person">
    <h1 class="person__name">DANA WHITFIELD</h1>
    <p class="person__role">Business Development Manager</p>
  </div>

  <ul class="contact">
    <li class="contact__item">
      <svg class="contact__icon" viewBox="0 0 16 16" aria-hidden="true"><path d="M3.5 1l2.6 2.8-1.4 2a9 9 0 0 0 5.5 5.5l2-1.4L15 12.5l-1.6 2.3C7.5 15 1 8.5 1.2 2.6z"/></svg>
      <span>+61 (0)7 3100 4820</span>
    </li>
    <li class="contact__item">
      <svg class="contact__icon" viewBox="0 0 16 16" aria-hidden="true"><path d="M3.5 1l2.6 2.8-1.4 2a9 9 0 0 0 5.5 5.5l2-1.4L15 12.5l-1.6 2.3C7.5 15 1 8.5 1.2 2.6z"/></svg>
      <span>+61 (0)7 3100 4827</span>
    </li>
    <li class="contact__item">
      <svg class="contact__icon" viewBox="0 0 16 16" aria-hidden="true"><path d="M4 0h8a1 1 0 0 1 1 1v14a1 1 0 0 1-1 1H4a1 1 0 0 1-1-1V1a1 1 0 0 1 1-1zm1 2v10h6V2zm3 11a1 1 0 1 0 0 2 1 1 0 0 0 0-2z"/></svg>
      <span>+61 (0)412 560 318</span>
    </li>
    <li class="contact__item">
      <svg class="contact__icon" viewBox="0 0 16 16" aria-hidden="true"><path d="M4 1h7l1 1v4H4zM1 7h14v6h-2v2H3v-2H1zm4 4v3h6v-3z"/></svg>
      <span>+61 (0)7 3100 4899</span>
    </li>
    <li class="contact__item">
      <svg class="contact__icon" viewBox="0 0 16 16" aria-hidden="true"><path d="M1 3h14v1L8 9 1 4zm0 3l7 5 7-5v7H1z"/></svg>
      <span>dwhitfield@korvalit.com.au</span>
    </li>
  </ul>

  <address class="address" style="font-style:normal">
    Level 1, 47 Fernby Street<br>Carlow Qld 4072
  </address>

  <div class="card__rule"></div>
  <div class="web-band">www.korvalit.com.au</div>
</section>

<section class="card card--back" aria-label="Business card back">
  <div class="brand">
    <span class="brand__mark"></span>
    <span class="brand__name">korvalit</span>
  </div>

  <ul class="services">
    <li class="service service--map"><span class="service__mark"></span>MapOut</li>
    <li class="service service--ship"><span class="service__mark"></span>ShipWell</li>
    <li class="service service--keep"><span class="service__mark"></span>KeepSteady</li>
  </ul>
</section>

</body>
</html>
```